NEW Modern Sleek Business Card for VR Language Startup

Our startup is using VR to lead the next wave of world language education. We need a two-sided business card that introduces the larger organization (Brightloom Language Inc) and our contact info on one side and shows the product, Glimwoorld, on the other side.

Side 1 (contact info)= Brightloom Logo and Contact info (name, title, phone, email)

Side 2 (product)= Glimworld logo, text, and website
Text= Culturally Immersive Language Learning Games
Website= www.glimworld-play.com

Target Market(s)

Education, Technology

Contact Information for Business Card

Contact info will be updated upon approval of the design. For now, put this as a placeholder.

Perry Dunmore
Founder & CEO
pdunmore@quillpost-mail.net
(555)-014-2286

Font styles to use
Other font styles liked:
• Gibson and Century Gothic are the brand fonts

Requirements
Nice to have
• I would love to see cohesion between the design and colors of the two logos. I have attached a few business card designs that I like, so you can get a feel for my preferred style.

```html
<!DOCTYPE html>
<html lang="en">
<head>
<meta charset="UTF-8">
<title>Brightloom Language – Business Card</title>
<link rel="stylesheet" href="https://fonts.googleapis.com/css2?family=Questrial&display=swap">
<style>
  :root {
    --page-bg: #111111;
    --card-bg: #1f1f1f;
    --text-light: #f2f2f2;
    --text-muted: #d9d9d9;
    --accent-blue: #36b4e8;
    --accent-red: #f0483e;
    --accent-purple: #8a5ad6;
    --card-shadow: rgba(0, 0, 0, 0.6);
  }
  * { box-sizing: border-box; margin: 0; padding: 0; }
  html, body {
    width: 1200px;
    height: 900px;
    overflow: hidden;
    background: var(--page-bg);
    font-family: "Questrial", "Century Gothic", sans-serif;
    color: var(--text-light);
  }
  .canvas {
    position: relative;
    width: 1200px;
    height: 900px;
    display: flex;
    flex-direction: column;
    align-items: center;
    justify-content: center;
    gap: 44px;
  }
  .card {
    position: relative;
    width: 640px;
    height: 366px;
    background: var(--card-bg);
    box-shadow: 0 18px 40px var(--card-shadow);
  }
  .brand {
    position: absolute;
    left: 0;
    right: 0;
    display: flex;
    align-items: center;
    justify-content: center;
    gap: 16px;
  }
  .brand-dot {
    width: 46px;
    height: 46px;
    border-radius: 50%;
    background: var(--accent-purple);
    flex: none;
  }
  .brand-name {
    font-size: 38px;
    letter-spacing: 4px;
    color: var(--text-light);
    line-height: 1;
    white-space: nowrap;
  }
  .card--product .brand { top: 96px; }
  .website {
    position: absolute;
    top: 218px;
    left: 0;
    right: 0;
    display: flex;
    align-items: center;
    justify-content: center;
    gap: 10px;
    font-size: 17px;
    color: var(--text-muted);
  }
  .tagline {
    position: absolute;
    top: 256px;
    left: 0;
    right: 0;
    text-align: center;
    font-size: 20px;
    color: var(--text-light);
    letter-spacing: 0.3px;
  }
  .card--contact .brand { top: 90px; }
  .contact-block {
    position: absolute;
    top: 220px;
    left: 0;
    right: 0;
    display: flex;
    justify-content: center;
    align-items: center;
    gap: 28px;
  }
  .person { text-align: right; }
  .person-name {
    font-size: 24px;
    color: var(--accent-blue);
    letter-spacing: 1.5px;
    text-transform: uppercase;
  }
  .person-title {
    font-size: 18px;
    color: var(--text-light);
    margin-top: 4px;
  }
  .divider {
    width: 2px;
    height: 62px;
    background: linear-gradient(to bottom, var(--accent-blue), var(--accent-purple), var(--accent-red));
  }
  .details { list-style: none; display: flex; flex-direction: column; gap: 10px; }
  .detail {
    display: flex;
    align-items: center;
    gap: 10px;
    font-size: 16px;
    color: var(--text-muted);
    white-space: nowrap;
  }
  .icon { width: 14px; height: 14px; flex: none; }
</style>
</head>
<body>
  <main class="canvas">
    <section class="card card--product" aria-label="Product side">
      <div class="brand">
        <span class="brand-dot"></span>
        <span class="brand-name">Glimworld</span>
      </div>
      <p class="website">
        <svg class="icon" viewBox="0 0 14 14" aria-hidden="true">
          <circle cx="7" cy="7" r="6" fill="var(--accent-blue)"/>
          <path d="M1 7h12M7 1c-2.5 3-2.5 9 0 12M7 1c2.5 3 2.5 9 0 12" stroke="var(--card-bg)" stroke-width="1" fill="none"/>
        </svg>
        www.glimworld-play.com
      </p>
      <p class="tagline">Culturally Immersive Language Learning Games</p>
    </section>

    <section class="card card--contact" aria-label="Contact side">
      <div class="brand">
        <span class="brand-dot"></span>
        <span class="brand-name">Brightloom Language</span>
      </div>
      <div class="contact-block">
        <div class="person">
          <p class="person-name">Perry Dunmore</p>
          <p class="person-title">Founder &amp; CEO</p>
        </div>
        <span class="divider"></span>
        <ul class="details">
          <li class="detail">
            <svg class="icon" viewBox="0 0 14 14" aria-hidden="true">
              <path d="M3 1.5l2.2 2.6-1.2 1.6c.8 1.8 2.3 3.3 4.3 4.3l1.6-1.2 2.6 2.2-1.3 1.7C6.5 12.5 1.5 7.5 1.3 2.8z" fill="var(--accent-blue)"/>
            </svg>
            (555)-014-2286
          </li>
          <li class="detail">
            <svg class="icon" viewBox="0 0 14 14" aria-hidden="true">
              <rect x="1" y="3" width="12" height="8.5" rx="1" fill="var(--accent-blue)"/>
              <path d="M1.5 3.8L7 8l5.5-4.2" stroke="var(--card-bg)" stroke-width="1.2" fill="none"/>
            </svg>
            pdunmore@quillpost-mail.net
          </li>
        </ul>
      </div>
    </section>
  </main>
</body>
</html>
```